Coaching landingpage/salespage need a layout

Hi!
We are two people from Sweden looking for help to design our coaching landingpage/salespage.

What about:
We need a nice modern timeless appealing Photoshop layout (landingpage) for our coaching page where we coach people to “how to get a richer lifestyle”.

Style of page:
We want the site to reflect seriousness but still harmonic. We would like somewhat colorful and (but not too crazy). After all, we are coaching about investments and private economy.
Responsive layout – consider stacking order when scaling down window width. Fullpage-design where content areas are 960 grid/max-width.

----------------------------------------------------------------------------
Content on page:
*Headersection – Logo and header image with the two coaches together and space for later on adding a video.

*On the landingpage the customers can read up on what we mean by a richer lifestyle (use dummy text). We show our Vardagskompassen (= Lifestyle matrix) and a little description about that. If the customers want to know more, they can click "read more (or a symbolic icon that relates to read more)" to expand a hidden div (section) where they can read more about Vardagskompassen. They can also minimize the section.

*3-4 Unique selling points “Four reasons why choose coaching” with nice designed number-icons and some place for text.

*The customer should also be able to read something about what happens during a typical coaching session, some bullets that summarize it (use dummy text) and a couple of headlines, maybe 3 or 4 (about what they need to prepare for themselves .eg Skype, headset/microphone etc).

*Offer/product section: A section where the customer can see what services we provide, choose product and click order. When customer click order they will arrive to an order-page (this one you don’t have to design) .
Our products are as followed: Bronze (single coaching session), Silver (small-package), Gold (large-package). Use provided graphics for these products.

*Testimonials section. Currently we have 2 good testimonials, but only with text no portrait picture.

Testimonial1: “Uppiggande och inspirerande! Kommer med enkla vardagstips såväl som svårare tips. Ett roligt sätt att få en spark i baken, så att ekonomi-energin bibehålls! Tack för ett bra samtal!" - Helena Brattvik

Testimonial2: "Värdefullast för mig var kunskapen om alternativa investeringssställen som inte är börs eller eget ägande." - Annika Sjöstedt

*Section with portraits and info about the coaches (currently 2 coaches, but in future will be several, so a design-section that’s lets us add more coaches).

*Footer-section
------------------------------------------------------------------------

Colors:
Use Vardagskompassen (attached file) as colorinspiration. Doesn’t have to be exactly those colors, you can use similar colors if it is more pleasing to the eye and you can also use complementary colors.

Currently we have tried of our own but don't really nail it with any apealing design. This is what we have done so far but we want to replace it with your more professional design:

https://www.harborkite.se/full/Page/coaching13
-------------------------------------------------------------

SUMMARIZE of the above design-description:

* Our logo (attached psd-file with smart-object. You can try different colors with color-overlay)

*Apealing headerimage with portrait (attached file "big_portrait")

*Introduction text (use dummy text about 100 words)

*Text about Vardagskompassen (use dummy text about 200 words)

*Vardagskompassen (attached psd-file with smart-object)

*What we are covering during a coaching session (dummy text about 200 words and about 5 or 6 bullets)

*3-4 Unique Selling Points with stylish number icons (not 2 small) and some text.
*Our offers Bronze, Silver, Gold (attached pictures)
*Testimonials
*Picture & info about coaches (attached pictures, choose whichever suits you)
*Footer

Please comment if there are questions.

Target Market(s)

People who want to learn how to create a richer lifestyle which involves more freedom and a better well-being

Number of Pages Required

1 page

Font styles to use
Sans Serif
Other font styles liked:
• Roboto

Requirements
Should not have
• A cheezy unmodern landingpage with lots of texts and 10 sign-up buttons.
• This page is not a site about capturing emails and building lists by provide a "best-guide-for-something". It´s about getting people to book and pay for one or more coaching-sessions.

```html
<!DOCTYPE html>
<html lang="en">
<head>
<meta charset="utf-8">
<title>Harbor Kite – Coaching</title>
<link rel="stylesheet" href="https://fonts.googleapis.com/css2?family=Montserrat:wght@400;600;700&family=Roboto:wght@300;400;500;700&display=swap">
<style>
:root{
  --blue:#2f9ad8;
  --blue-dark:#1f7fbf;
  --ink:#1f1f1f;
  --text:#444;
  --muted:#777;
  --light:#efefef;
  --rule:#cfcfcf;
  --brown:#8c7163;
  --orange:#f6a623;
  --green:#2db56f;
  --footer-dark:#151515;
  --white:#fff;
}
*{box-sizing:border-box;margin:0;padding:0}
html,body{width:1200px;height:3593px;overflow:hidden}
body{font-family:"Roboto",Arial,sans-serif;color:var(--text);background:var(--white);position:relative}
.abs{position:absolute}
.heading{font-family:"Montserrat",Arial,sans-serif;font-weight:600;font-size:31px;color:var(--ink);text-align:center;position:absolute;left:0;width:1200px}
.heading span{color:var(--blue);font-weight:400}
.divider{position:absolute;left:430px;width:340px;height:1px;background:var(--rule)}
.divider::after{content:"";position:absolute;left:162px;top:-8px;width:16px;height:16px;background:var(--blue)}
.btn-outline{position:absolute;border:1.5px solid #555;background:var(--white);font-size:13px;color:var(--ink);display:flex;align-items:center;justify-content:center;gap:9px}
.btn-outline i{display:inline-block;width:16px;height:16px;border:1.5px solid #333;border-radius:50%;position:relative}
.btn-outline i::after{content:"";position:absolute;left:3px;top:4px;width:5px;height:5px;border-top:1.5px solid #333;border-right:1.5px solid #333;transform:rotate(45deg)}

/* header */
.site-header{position:absolute;left:0;top:0;width:1200px;height:91px;background:var(--white)}
.brand{position:absolute;left:100px;top:26px;display:flex;align-items:center;gap:12px}
.brand-mark{width:34px;height:34px;background:var(--blue)}
.brand-name{font-family:"Montserrat",Arial,sans-serif;font-size:26px;font-weight:400;color:var(--blue);letter-spacing:1px;text-transform:uppercase}
.header-call{position:absolute;left:866px;top:26px;display:flex;gap:10px;align-items:center}
.header-call small{display:block;font-size:11px;font-weight:700;color:var(--ink)}
.header-call strong{display:block;font-size:21px;font-weight:400;color:var(--ink)}
.header-social{position:absolute;left:1068px;top:30px;width:30px;height:30px;background:#3b5998}

/* hero */
.hero{position:absolute;left:0;top:91px;width:1200px;height:513px;background:linear-gradient(100deg,#3a3c40 0%,#8c8f94 35%,#c9ced4 60%,#9aa1a9 100%)}
.hero-kicker{position:absolute;left:100px;top:230px;color:var(--white);font-family:"Montserrat",Arial,sans-serif;font-size:29px;font-weight:400}
.hero-title{position:absolute;left:100px;top:268px;color:var(--white);font-family:"Montserrat",Arial,sans-serif;font-size:44px;font-weight:400}
.hero-btn{position:absolute;left:100px;top:340px;width:165px;height:38px;background:var(--blue);color:var(--white);font-size:13px;display:flex;align-items:center;justify-content:center;gap:8px}
.hero-btn i{width:17px;height:17px;border:1.5px solid var(--white);border-radius:50%;position:relative}
.hero-btn i::after{content:"";position:absolute;left:5px;top:3px;border-left:6px solid var(--white);border-top:4px solid transparent;border-bottom:4px solid transparent}
.hero-video{position:absolute;left:663px;top:156px;width:434px;height:292px;border:6px solid var(--white);background:linear-gradient(180deg,#f0b35a 0%,#d78a3a 45%,#3d3a36 100%);box-shadow:0 3px 10px rgba(0,0,0,.35)}
.video-bar{position:absolute;left:0;bottom:0;width:100%;height:36px;background:#1b1b1b}
.video-progress{position:absolute;left:24px;top:16px;width:300px;height:4px;background:#666}
.video-progress::before{content:"";position:absolute;left:0;top:0;width:175px;height:4px;background:#d2231e}

/* about */
.about-text{position:absolute;left:100px;top:772px;width:1000px;text-align:center;font-size:12.5px;line-height:24px;color:var(--text)}

/* matrix */
.matrix{position:absolute;left:0;top:987px;width:1200px;height:558px;background:var(--light)}
.matrix-sub{position:absolute;left:0;top:127px;width:1200px;text-align:center;font-size:17px;font-weight:700;color:var(--ink)}
.matrix-intro{position:absolute;left:100px;top:160px;width:1000px;text-align:center;font-size:12.5px;line-height:23px}
.stage{position:absolute;top:258px;width:180px;text-align:center}
.stage .dot{width:108px;height:108px;border-radius:50%;margin:0 auto;display:flex;align-items:center;justify-content:center}
.stage h3{margin-top:30px;font-family:"Montserrat",Arial,sans-serif;font-size:17px;font-weight:600;line-height:22px}
.stage h3 span{display:block;font-weight:400;color:var(--muted)}
.stage p{margin-top:14px;font-size:12.5px;line-height:18px;color:var(--text)}

/* coaching */
.coaching{position:absolute;left:0;top:1545px;width:1200px;height:479px;background:linear-gradient(180deg,#3ba4de,#2b8fcf)}
.coaching .heading{color:var(--white)}
.coaching .heading span{color:var(--white);font-weight:300}
.coaching .divider{background:rgba(255,255,255,.5)}
.coaching .divider::after{background:var(--white)}
.coaching-image{position:absolute;left:115px;top:167px;width:345px;height:248px;background:linear-gradient(160deg,#f4f4f4,#c9d6e2);border:4px solid var(--white)}
.benefits{position:absolute;left:532px;top:170px;width:570px;list-style:none}
.benefits li{color:var(--white);font-size:13px;line-height:20px;margin-bottom:22px;padding-left:26px;position:relative}
.benefits li::before{content:"";position:absolute;left:0;top:5px;border-left:8px solid var(--white);border-top:5px solid transparent;border-bottom:5px solid transparent}

/* products */
.product{position:absolute;top:2215px;width:220px;text-align:center}
.medal{width:152px;height:152px;border-radius:50%;margin:0 auto}
.product h3{margin-top:22px;font-size:18px;font-weight:700;color:var(--ink)}
.product p{margin-top:4px;font-size:13px;color:var(--ink)}

/* testimonials */
.testimonials{position:absolute;left:0;top:2558px;width:1200px;height:412px;background:linear-gradient(180deg,#e9e9e9,#f6f6f6)}
.quote{position:absolute;top:184px;width:360px;height:104px;background:var(--white);border:1px solid #ddd;padding:14px 18px 0 54px;font-size:12px;line-height:17px;color:var(--muted)}
.quote::before{content:"\201C";position:absolute;left:14px;top:2px;font-size:52px;color:#bbb;font-family:Georgia,serif}
.quote::after{content:"";position:absolute;left:40px;bottom:-12px;border-top:12px solid var(--white);border-right:14px solid transparent}
.quote-name{position:absolute;top:309px;font-size:12.5px;font-weight:700;color:var(--ink)}

/* coaches */
.coach-photo{position:absolute;top:3157px;width:214px;height:172px;background:linear-gradient(160deg,#b9c3ca,#6e7a83)}
.coach-info{position:absolute;top:3152px;width:236px}
.coach-info h3{font-size:14px;font-weight:700;color:var(--ink);margin-bottom:10px}
.coach-info p{font-size:12.5px;line-height:18.5px;text-align:justify;color:var(--text)}

/* footer */
.footer-nav{position:absolute;left:0;top:3401px;width:1200px;height:65px;background:var(--footer-dark);display:flex;align-items:center;padding-left:106px;color:var(--white);font-size:13px;font-weight:500}
.footer-nav .sep{margin:0 38px}
.footer-social{position:absolute;left:1071px;top:3424px;width:20px;height:20px;background:#8a8a8a}
.footer-main{position:absolute;left:0;top:3466px;width:1200px;height:127px;background:var(--blue)}
.contact{position:absolute;top:44px;display:flex;gap:12px;color:var(--white);font-size:11.5px;line-height:15px}
.contact .ico{width:28px;height:28px;border-radius:50%;background:#111;flex:none;display:flex;align-items:center;justify-content:center}
.contact b{display:block;font-weight:700}
.footer-brand{position:absolute;left:848px;top:38px;color:var(--white)}
.footer-brand .name{font-family:"Montserrat",Arial,sans-serif;font-size:21px;letter-spacing:1px;text-transform:uppercase;display:flex;align-items:center;gap:10px}
.footer-brand .name i{width:26px;height:26px;background:var(--white)}
.footer-brand small{display:block;margin-top:10px;font-size:11px}
</style>
</head>
<body>

<header class="site-header">
  <div class="brand"><div class="brand-mark"></div><div class="brand-name">Harbor Kite</div></div>
  <div class="header-call">
    <svg width="26" height="26" viewBox="0 0 24 24"><path d="M6.6 10.8a15 15 0 0 0 6.6 6.6l2.2-2.2c.3-.3.7-.4 1-.2 1.1.4 2.3.6 3.6.6.6 0 1 .4 1 1V20c0 .6-.4 1-1 1A17 17 0 0 1 3 4c0-.6.4-1 1-1h3.5c.6 0 1 .4 1 1 0 1.3.2 2.5.6 3.6.1.3 0 .7-.2 1z" fill="#222"/></svg>
    <div><small>CALL US NOW!</small><strong>(013) 482 1057</strong></div>
  </div>
  <div class="header-social" aria-label="Social page"></div>
</header>

<section class="hero">
  <div class="abs" role="img" aria-label="Photo of a woman stepping out of a luxury car beside a private jet" style="inset:0"></div>
  <div class="hero-kicker">Step By Step To</div>
  <div class="hero-title">A Richer Lifestyle</div>
  <div class="hero-btn">Watch Our Video <i></i></div>
  <div class="hero-video" role="img" aria-label="Video still of the two coaches standing together outdoors at sunset">
    <div class="video-bar"><div class="video-progress"></div></div>
  </div>
</section>

<section>
  <h2 class="heading" style="top:690px">Know About <span>Harbor Kite</span></h2>
  <div class="divider" style="top:746px"></div>
  <p class="about-text">Lorem ipsum dolor sit amet, consectetuer adipiscing elit, sed diam nonummy nibh euismod tincidunt ut laoreet dolore magna aliquam erat volutpat. Ut wisi enim ad minim veniam, quis nostrud exerci tation ullamcorper suscipit lobortis nisl ut aliquip ex ea commodo consequat. Duis autem vel eum iriure dolor in hendrerit in vulputate velit esse molestie consequat, vel illum dolore eu feugiat nulla facilisis at vero eros et accumsan et iusto odio dignissim qui blandit praesent luptatum zzril nulla facilisis at &nbsp;vel illum dolore vero eros et &nbsp;odio delenit &nbsp;nulla facilisit.</p>
  <div class="btn-outline" style="left:537px;top:897px;width:126px;height:36px">Read More <i></i></div>
</section>

<section class="matrix">
  <h2 class="heading" style="top:42px">Our <span>Lifestyle Matrix</span></h2>
  <div class="divider" style="top:97px"></div>
  <div class="matrix-sub">What Is A Richer Lifestyle?</div>
  <p class="matrix-intro">What is a richer lifestyle may differ between different people. It can also be quite difficult on their own to get a good picture of what you really mean by this . We have therefore developed a simple model to facilitate the understanding and the creation of a richer lifestyle. This is a model we call lifestyle matrix and consists of the following four parts representing respective lifestyle.</p>

  <svg class="abs" style="left:0;top:230px" width="1200" height="80" viewBox="0 0 1200 80" fill="none" stroke="#8a8a8a" stroke-width="1.5">
    <path d="M355 46 Q392 10 428 36"/><path d="M422 30 L429 37 L420 40"/>
    <path d="M555 46 Q592 10 628 36"/><path d="M622 30 L629 37 L620 40"/>
    <path d="M755 46 Q792 10 828 36"/><path d="M822 30 L829 37 L820 40"/>
  </svg>

  <div class="stage" style="left:202px">
    <div class="dot" style="background:var(--brown)"><svg width="52" height="52" viewBox="0 0 52 52" fill="none" stroke="#fff" stroke-width="3"><circle cx="26" cy="26" r="20"/><path d="M26 26 L36 16"/></svg></div>
    <h3 style="color:var(--brown)">RAT RACE<span>LIFESTYLE</span></h3>
    <p>Lorem ipsum dolor sit amet, consectetuer adipiscing elit, sed diam nonummy</p>
  </div>
  <div class="stage" style="left:403px">
    <div class="dot" style="background:var(--blue)"><svg width="52" height="52" viewBox="0 0 24 24"><path d="M12 21s-8-5.2-8-11a4.5 4.5 0 0 1 8-2.8A4.5 4.5 0 0 1 20 10c0 5.8-8 11-8 11z" fill="#fff"/></svg></div>
    <h3 style="color:var(--blue)">PROSPEROUS<span>LIFESTYLE</span></h3>
    <p>Lorem ipsum dolor sit amet, consectetuer adipiscing elit, sed diam nonummy</p>
  </div>
  <div class="stage" style="left:602px">
    <div class="dot" style="background:var(--orange)"><svg width="52" height="52" viewBox="0 0 52 52" fill="none" stroke="#fff" stroke-width="3"><circle cx="26" cy="26" r="18"/><path d="M26 14v24M31 19h-7a4 4 0 0 0 0 8h4a4 4 0 0 1 0 8h-7"/></svg></div>
    <h3 style="color:var(--orange)">A RICHER<span>LIFESTYLE</span></h3>
    <p>Lorem ipsum dolor sit amet, consectetuer adipiscing elit, sed diam nonummy</p>
  </div>
  <div class="stage" style="left:801px">
    <div class="dot" style="background:var(--green)"><svg width="52" height="52" viewBox="0 0 52 52" fill="none" stroke="#fff" stroke-width="3.5"><path d="M26 40V14M15 24l11-11 11 11"/></svg></div>
    <h3 style="color:var(--green)">FREEDOM<span>LIFESTYLE</span></h3>
    <p>Lorem ipsum dolor sit amet, consectetuer adipiscing elit, sed diam nonummy</p>
  </div>
</section>

<section class="coaching">
  <h2 class="heading" style="top:60px">Why <span>Choose Coaching</span></h2>
  <div class="divider" style="top:115px"></div>
  <div class="coaching-image" role="img" aria-label="Jigsaw puzzle pieces with a blue piece labelled coaching"></div>
  <ul class="benefits">
    <li>Lorem ipsum dolor sit amet, consectetuer adipiscing elit, sed diam nonummy nibh tinonummy ncidunt.</li>
    <li>Ut wisi enimeniam, quis nostrud exerci tation ullamcorper suscipit lo ut aliquip..</li>
    <li>Accumsan et iusto odio dignissim qui blandit praesent luptatum zzril nulla facilisis at vel illuhendrerit in vulputate hendrerit in vulputate</li>
    <li>Commodo consequat. Duis autem vel eum iriur dolor in hendrerit in vulputate velit consequa ullamcorper suscipit..</li>
  </ul>
</section>

<section>
  <h2 class="heading" style="top:2103px">Our <span>Products</span></h2>
  <div class="divider" style="top:2159px"></div>
  <div class="product" style="left:160px">
    <div class="medal" role="img" aria-label="Bronze product badge" style="background:radial-gradient(circle at 40% 35%,#f0a66b,#c8672a 60%,#8e4515)"></div>
    <h3>Bronze</h3><p>Single Coaching Session</p>
  </div>
  <div class="product" style="left:490px">
    <div class="medal" role="img" aria-label="Gold product badge" style="background:radial-gradient(circle at 40% 35%,#fde27a,#e5b317 60%,#a87d06)"></div>
    <h3>Gold</h3><p>Small - Package</p>
  </div>
  <div class="product" style="left:812px">
    <div class="medal" role="img" aria-label="Silver product badge" style="background:radial-gradient(circle at 40% 35%,#f5f5f5,#bdbdbd 60%,#858585)"></div>
    <h3>Silver</h3><p>Large - Package</p>
  </div>
  <div class="btn-outline" style="left:172px;top:2443px;width:196px;height:34px">Make An Appointment <i></i></div>
  <div class="btn-outline" style="left:507px;top:2443px;width:186px;height:34px">Make An Appointment <i></i></div>
  <div class="btn-outline" style="left:834px;top:2443px;width:186px;height:34px">Make An Appointment <i></i></div>
</section>

<section class="testimonials" role="img" aria-label="Faint grid of client portrait photos behind the testimonials">
  <h2 class="heading" style="top:62px">Client <span>Testimonial</span></h2>
  <div class="divider" style="top:117px"></div>
  <div class="quote" style="left:215px">" Uppiggande och inspirerande! Kommer med enkla vardagstips såväl som svårare tips. Ett roligt sätt att få en spark i baken, så att ekonomi-energin bibehålls! Tack för ett bra samtal! "</div>
  <div class="quote-name" style="left:245px">Mr. Helena Brattvik</div>
  <div class="quote" style="left:620px">" Värdefullast för mig var kunskapen om alternativa investeringssställen som inte är börs eller eget ägande. "</div>
  <div class="quote-name" style="left:650px">Mr. Annika Sjöstedt</div>
</section>

<section>
  <h2 class="heading" style="top:3035px">Our <span>Coaches</span></h2>
  <div class="divider" style="top:3091px"></div>
  <div class="coach-photo" style="left:98px" role="img" aria-label="Portrait photo of coach Joakim Hedström"></div>
  <div class="coach-info" style="left:342px">
    <h3>Mr. Joakim Hedström</h3>
    <p>Mångsidig investerare med fokus på alternativa och högriskinvesteringar. Förutom börsen, investerar Joakim i onoterade startup-bolag och olika internetbaserade investeringar såsom P2P-lending, onlinespel och appar.</p>
  </div>
  <div class="coach-photo" style="left:618px" role="img" aria-label="Portrait photo of coach Mattias Lindqvist"></div>
  <div class="coach-info" style="left:866px">
    <h3>Mr. Mattias Lindqvist</h3>
    <p>Mattias har en bred bakgrund inom ekonomi och IT. Som investerare ligger hans fokus på utdelningsaktier, fastigheter och internetbaserat entreprenörskap. Han har också en lång erfarenhet och en stor passion av att hjälpa människor...[+]</p>
  </div>
</section>

<nav class="footer-nav">
  <span>BLOG</span><span class="sep">|</span><span>COACHING</span><span class="sep">|</span><span>ABOUT US</span>
</nav>
<div class="footer-social" aria-label="Social page"></div>

<footer class="footer-main">
  <div class="contact" style="left:100px">
    <div class="ico"><svg width="14" height="14" viewBox="0 0 24 24"><path d="M12 2a7 7 0 0 0-7 7c0 5 7 13 7 13s7-8 7-13a7 7 0 0 0-7-7zm0 9.5A2.5 2.5 0 1 1 12 6.5a2.5 2.5 0 0 1 0 5z" fill="#fff"/></svg></div>
    <div><b>HARBOR KITE</b>Harbor Kite AB Ekbacksgatan 12<br>412 63 Göteborg</div>
  </div>
  <div class="contact" style="left:384px">
    <div class="ico"><svg width="14" height="14" viewBox="0 0 24 24"><path d="M6.6 10.8a15 15 0 0 0 6.6 6.6l2.2-2.2c.3-.3.7-.4 1-.2 1.1.4 2.3.6 3.6.6.6 0 1 .4 1 1V20c0 .6-.4 1-1 1A17 17 0 0 1 3 4c0-.6.4-1 1-1h3.5c.6 0 1 .4 1 1 0 1.3.2 2.5.6 3.6.1.3 0 .7-.2 1z" fill="#fff"/></svg></div>
    <div><b>CALL US :</b><b>013. 482. 1057</b></div>
  </div>
  <div class="contact" style="left:604px">
    <div class="ico"><svg width="14" height="14" viewBox="0 0 24 24"><path d="M3 6h18v12H3z" fill="#fff"/><path d="M3 6l9 7 9-7" fill="none" stroke="#111" stroke-width="1.5"/></svg></div>
    <div><b>EMAIL US :</b>team@harborkite.se</div>
  </div>
  <div class="footer-brand">
    <div class="name"><i></i>Harbor Kite</div>
    <small>© 2016 Harborkite. All Rights Reserved.</small>
  </div>
</footer>

</body>
</html>
```